Card Design for my dog training business Brightpaw Obedience

Need a business card design for my dog training business with my new logo. Want the card to come off professional yet fun. Want it to be very eye catchy as well. I normally have these at vet clinics, pet stores, and groomers. so need it to look better than my competitors.
Target Market(s)
dog owners
Industry/Entity Type
Dog Training
Contact Information for Business Card
needs logo, my name and info
Font styles to use
Serif
Colors
0255a3
ffffff
ec1f27
000000
333333
fbfbfb
Requirements
Must have
- Brightpaw Obedience
- Felix Orland
- 415 903 2276
- info@brightpawobedience.example
- www.brightpawobedience.example

```html
<!DOCTYPE html>
<html lang="en">
<head>
<meta charset="utf-8">
<title>Brightpaw Obedience — Business Card</title>
<link rel="stylesheet" href="https://fonts.googleapis.com/css2?family=EB+Garamond:ital,wght@0,500;1,400&family=Roboto:wght@300;400&display=swap">
<style>
  :root {
    --page: #e4e4e4;
    --card: #f6f6f6;
    --panel: #1c1c1c;
    --panel-art: #2a2a2a;
    --ink: #111111;
    --name-ink: #d6d6d6;
    --contact-ink: #bdbdbd;
    --icon: #e2e2e2;
  }
  * { margin: 0; padding: 0; box-sizing: border-box; }
  html, body { width: 1125px; height: 1200px; overflow: hidden; }
  body { background: var(--page); position: relative; font-family: "Roboto", sans-serif; }

  .card {
    position: absolute;
    left: 150px;
    width: 825px;
    height: 472px;
    background: var(--card);
    overflow: hidden;
    box-shadow: 0 2px 5px rgba(0,0,0,0.25);
  }
  .card--front { top: 98px; }
  .card--back { top: 630px; }

  .front-panel { position: absolute; inset: 0; width: 825px; height: 472px; }

  .front-brand {
    position: absolute;
    left: 31px;
    top: 250px;
    width: 245px;
    text-align: center;
    font-family: "EB Garamond", serif;
    font-weight: 500;
    font-size: 36px;
    line-height: 1.05;
    color: var(--ink);
  }
  .front-brand .mark {
    display: block;
    width: 14px; height: 14px;
    background: var(--ink);
    border-radius: 50%;
    margin: 0 auto 14px;
  }

  .contact {
    position: absolute;
    right: 63px;
    top: 293px;
    text-align: right;
    color: var(--contact-ink);
  }
  .contact__name {
    font-size: 26px;
    font-weight: 400;
    letter-spacing: 0.5px;
    color: var(--name-ink);
    margin-bottom: 17px;
  }
  .contact__line {
    display: flex;
    justify-content: flex-end;
    align-items: center;
    gap: 12px;
    font-size: 19px;
    font-weight: 300;
    height: 26px;
  }
  .contact__line svg { width: 17px; height: 17px; flex: none; }

  .back-brand {
    position: absolute;
    left: 0; right: 0;
    top: 160px;
    text-align: center;
    font-family: "EB Garamond", serif;
    font-weight: 500;
    font-size: 66px;
    color: var(--ink);
  }
  .back-brand .mark {
    display: block;
    width: 18px; height: 18px;
    background: var(--ink);
    border-radius: 50%;
    margin: 0 auto 20px;
  }
  .tagline {
    position: absolute;
    left: 0; right: 0;
    top: 404px;
    text-align: center;
    font-family: "EB Garamond", serif;
    font-style: italic;
    font-size: 24px;
    color: var(--ink);
  }
</style>
</head>
<body>

<section class="card card--front">
  <svg class="front-panel" viewBox="0 0 825 472" aria-hidden="true">
    <path d="M562 0 H825 V472 H408 C470 360 520 200 562 0 Z" fill="var(--panel)"/>
  </svg>
  <svg class="front-panel" viewBox="0 0 825 472" role="img" aria-label="Large dark illustration of two dog heads in profile">
    <path d="M370 20 C420 10 520 0 600 20 C700 60 800 140 815 260 C825 360 800 440 780 472 H400 C380 420 340 320 315 270 C330 180 340 90 370 20 Z" fill="var(--panel-art)" opacity="0.85"/>
  </svg>

  <div class="front-brand"><span class="mark"></span>Brightpaw<br>Obedience</div>

  <div class="contact">
    <div class="contact__name">FELIX ORLAND</div>
    <div class="contact__line">415 903 2276
      <svg viewBox="0 0 24 24"><path fill="var(--icon)" d="M6.6 10.8a15.2 15.2 0 0 0 6.6 6.6l2.2-2.2a1 1 0 0 1 1-.25 11.4 11.4 0 0 0 3.6.57 1 1 0 0 1 1 1V20a1 1 0 0 1-1 1A17 17 0 0 1 3 4a1 1 0 0 1 1-1h3.5a1 1 0 0 1 1 1c0 1.25.2 2.45.57 3.57a1 1 0 0 1-.25 1z"/></svg>
    </div>
    <div class="contact__line">info@brightpawobedience.example
      <svg viewBox="0 0 24 24"><rect x="2" y="5" width="20" height="14" fill="var(--icon)"/><path d="M2 5 L12 13 L22 5" fill="none" stroke="var(--panel)" stroke-width="1.6"/></svg>
    </div>
    <div class="contact__line">brightpawobedience.example
      <svg viewBox="0 0 24 24"><circle cx="12" cy="12" r="10" fill="var(--icon)"/><path d="M7 8c2 0 3 2 2 4s1 3 2 5M14 5c0 2 2 3 4 3M15 14c1 0 3 1 3 3" fill="none" stroke="var(--panel)" stroke-width="1.6"/></svg>
    </div>
  </div>
</section>

<section class="card card--back">
  <div class="back-brand"><span class="mark"></span>Brightpaw Obedience</div>
  <p class="tagline">“Training dogs across Texas one dog at a time.”</p>
</section>

</body>
</html>
```